Custom Cabinet Shop Needs a website design

Hi,
We need a website for a Custom Cabinet Shop and Cabinet parts manufacturing business.
The business has two sides to it. One side provides custom Kitchens, vanities, entertainment units, offices and what not to homeowners and contractors.
The 2nd side of the business provides built to order cabinet boxes and other parts required to put together a project to other cabinet shops, small contractors looking to install there own cabinets.
Website will need a Gallery to display work.
Color scheme to go well with logo.
current website is www.brambleoakcustomcabinets.com
being changed to www.brambleoak.ca
Logo Included in attached files.
Tagline "Joinery with Spirit"
Mission Statement "Our passion is to deliver inspired cabinetry solutions to suit all your needs, supported by our phenomenal star class customer service"
The website should convey quality and professionalism.
Thank you.
Homeowners/ Contractors
Entertainment

```html
<!DOCTYPE html>
<html lang="en">
<head>
<meta charset="utf-8">
<title>Brambleoak Custom Cabinets</title>
<link rel="stylesheet" href="https://fonts.googleapis.com/css2?family=Cabin:wght@400;500;600;700&family=PT+Sans:wght@400;700&display=swap">
<style>
:root{
  --orange:#e35a24;
  --charcoal:#1c1a18;
  --text:#555;
  --white:#fff;
}
*{margin:0;padding:0;box-sizing:border-box}
html,body{width:863px;height:1200px;overflow:hidden;background:var(--white)}
body{position:relative;font-family:"PT Sans",sans-serif;color:var(--text)}
a{text-decoration:none}
.page{position:relative;width:863px;height:1200px}

.hero-photo{position:absolute;left:0;top:0;width:863px;height:477px;
  background:
    radial-gradient(ellipse 260px 70px at 470px 300px,rgba(214,160,110,.75),rgba(214,160,110,0) 100%),
    radial-gradient(ellipse 120px 90px at 150px 260px,rgba(190,140,90,.45),rgba(190,140,90,0) 100%),
    linear-gradient(90deg,#1c2530 0%,#2a3340 22%,rgba(42,51,64,0) 38%),
    linear-gradient(180deg,#d8d2c8 0%,#b3a493 14%,#6f5a48 30%,#8a6c52 50%,#5a4434 68%,#7a5538 82%,#4d3423 100%)}

.site-header{position:absolute;left:0;top:0;width:863px;height:58px;
  background:linear-gradient(180deg,#2a2725,#171514);border-bottom:1px solid #000}
.main-nav a{position:absolute;top:22px;font-family:"Cabin",sans-serif;font-size:13px;color:var(--white)}
.main-nav a.is-active{color:var(--orange)}

.brand-tab{position:absolute;left:354px;top:0;width:168px;height:93px}
.brand-name{position:absolute;left:354px;top:30px;width:168px;display:flex;align-items:center;justify-content:center;gap:6px;
  font-family:"Cabin",sans-serif;font-weight:700;font-size:16px;color:var(--charcoal);letter-spacing:.5px}
.brand-dot{width:12px;height:12px;border-radius:50%;background:var(--orange)}

.promo-band{position:absolute;left:0;top:477px;width:863px;height:98px;background:var(--orange)}
.promo-title{position:absolute;left:79px;top:16px;font-family:"Cabin",sans-serif;font-weight:400;font-size:29px;color:var(--white);letter-spacing:-.5px;text-transform:uppercase}
.promo-title strong{font-weight:700}
.promo-text{position:absolute;left:79px;top:54px;width:500px;font-size:8.5px;line-height:14px;color:var(--white)}
.btn-dark{position:absolute;background:var(--charcoal);color:var(--white);font-family:"Cabin",sans-serif;font-weight:600;display:flex;align-items:center;justify-content:center;border-radius:2px;box-shadow:0 2px 0 #000}
.promo-btn{left:650px;top:32px;width:134px;height:36px;font-size:11px}

.intro{position:absolute;left:65px;top:575px;width:734px;height:215px;background:var(--white);box-shadow:0 0 6px rgba(0,0,0,.15)}
.intro-cover{position:absolute;left:0;top:650px;width:863px;height:140px;background:var(--white)}
.feature{position:absolute;top:612px;width:232px}
.feature h2{font-family:"Cabin",sans-serif;font-weight:500;font-size:14px;color:var(--orange);text-transform:uppercase;padding-left:21px;position:relative}
.feature h2::before{content:"";position:absolute;left:0;top:2px;width:5px;height:12px;background:var(--orange)}
.feature-body{margin-top:25px;border-left:3px dotted #ebe9e6;padding-left:18px;height:108px;font-size:9.3px;line-height:16px;color:#555}
.feature .btn-dark{height:24px;font-size:9px;width:61px}

.gallery{position:absolute;left:0;top:790px;width:863px;height:263px;background:linear-gradient(90deg,#ececea,#f7f7f5 50%,#ececea)}
.gallery-title{position:absolute;left:79px;top:28px;font-family:"Cabin",sans-serif;font-weight:500;font-size:14px;color:var(--charcoal)}
.gallery-rule{position:absolute;left:178px;top:38px;width:570px;border-top:3px dotted #dcdad6}
.gallery-arrow{position:absolute;top:33px;width:12px;height:12px;display:flex;align-items:center;justify-content:center}
.card{position:absolute;top:66px;width:165px;height:160px;border-bottom:2px solid #c9c7c3}
.card-photo{width:165px;height:122px}
.card-caption{height:36px;text-align:center;padding-top:6px}
.card-caption h3{font-family:"Cabin",sans-serif;font-weight:400;font-size:11px;color:#333}
.card-caption p{font-size:7.5px;color:#999;margin-top:2px}
.card.is-hover{border-bottom-color:var(--orange)}
.card.is-hover .card-caption{background:var(--orange)}
.card.is-hover h3,.card.is-hover p{color:var(--white)}
.card-overlay{position:absolute;left:0;top:0;width:165px;height:122px;background:#141312;display:flex;align-items:center;justify-content:center}

.site-footer{position:absolute;left:0;top:1055px;width:863px;height:145px;background:linear-gradient(180deg,#2b2825,#1b1917)}
.footer-nav{position:absolute;top:30px;left:0;width:863px;display:flex;justify-content:center}
.footer-nav a{font-family:"Cabin",sans-serif;font-size:10.5px;color:var(--white);margin:0 14px}
.footer-nav a.is-active{font-weight:700}
.social{position:absolute;top:63px;left:0;width:863px;display:flex;justify-content:center;gap:6px}
.social-link{width:20px;height:20px;border-radius:50%;background:var(--white);display:flex;align-items:center;justify-content:center}
.social-link::after{content:"";width:12px;height:12px;border-radius:50%;border:2px solid #2a2725}
.copyright{position:absolute;top:103px;left:0;width:863px;text-align:center;font-family:"Cabin",sans-serif;font-size:8.5px;color:var(--white)}
</style>
</head>
<body>
<div class="page">

  <div class="hero-photo" role="img" aria-label="Photo of a basement bar with live-edge wood counter, stone base, bar stools and pendant lights"></div>

  <header class="site-header">
    <nav class="main-nav">
      <a href="#" class="is-active" style="left:103px">Home</a>
      <a href="#" style="left:172px">Our Gallery</a>
      <a href="#" style="left:268px">Our Services</a>
      <a href="#" style="left:587px">Warranty</a>
      <a href="#" style="left:671px">Contact Us</a>
    </nav>
  </header>

  <svg class="brand-tab" viewBox="0 0 168 93" aria-hidden="true">
    <polygon points="0,0 168,0 168,93 84,78 0,93" fill="#fff"/>
  </svg>
  <div class="brand-name"><span class="brand-dot"></span>BRAMBLEOAK</div>

  <section class="promo-band">
    <h1 class="promo-title">Joinery with <strong>Spirit</strong></h1>
    <p class="promo-text">Lorem ipsum dolor sit amet, consectetur adipiscing elit sed do eiusmod tempor incididunt ut labore et dolore enim minim veniam, quis nostrud exercitation ullamco laboris nisi ut aliquip ex ea commodo consequat &nbsp;dolor in reprehenderit .</p>
    <a class="btn-dark promo-btn" href="#">READ MORE</a>
  </section>

  <div class="intro"></div>
  <div class="intro-cover"></div>

  <article class="feature" style="left:80px">
    <h2>About Us</h2>
    <div class="feature-body">Lorem ipsum dolor sit amet, consectetur adipiscing elit, sed do eiusmod tempor incididunt ut labore et dolore magna aliqua the iut enm ad minim veniam quis nostrud exercitation ullamco the a ilaboris nisi aliquip ex ea commodo consequat.</div>
  </article>
  <article class="feature" style="left:322px">
    <h2>Finest Quality Materials</h2>
    <div class="feature-body">Lorem ipsum dolor sit amet, consectetur adipiscing elit, sed do eiusmod tempor incididunt ut labore et dolore magna aliqua enim ad minim veniam is quis exercitation ullamco.</div>
    <a class="btn-dark" href="#" style="left:154px;top:113px">Read More</a>
  </article>
  <article class="feature" style="left:564px">
    <h2>Residential</h2>
    <div class="feature-body">Here at Brambleoak Custom Cabinets we are proud to be involved in the custom cabinet market. By employing and partnering up with local artisans we are able to deliver a product.</div>
    <a class="btn-dark" href="#" style="left:159px;top:113px">Read More</a>
  </article>

  <section class="gallery">
    <h2 class="gallery-title">OUR GALLERY</h2>
    <div class="gallery-rule"></div>
    <span class="gallery-arrow" style="left:758px;background:#6b6966">
      <svg width="6" height="6" viewBox="0 0 6 6"><path d="M4 0.5 1.5 3 4 5.5" stroke="#fff" fill="none" stroke-width="1.2"/></svg>
    </span>
    <span class="gallery-arrow" style="left:772px;background:var(--orange)">
      <svg width="6" height="6" viewBox="0 0 6 6"><path d="M2 0.5 4.5 3 2 5.5" stroke="#fff" fill="none" stroke-width="1.2"/></svg>
    </span>

    <div class="card" style="left:80px">
      <div class="card-photo" role="img" aria-label="Photo of a kitchen with cherry cabinets and a central island" style="background:linear-gradient(160deg,#a98a6c,#6b2e1c 60%,#4a1e12)"></div>
      <div class="card-caption"><h3>Lorem Ipsum Dolor</h3><p>Lorem ipsum</p></div>
    </div>
    <div class="card is-hover" style="left:259px">
      <div class="card-photo"></div>
      <div class="card-overlay">
        <svg width="30" height="30" viewBox="0 0 30 30" aria-hidden="true">
          <circle cx="12" cy="12" r="9" fill="none" stroke="#fff" stroke-width="3"/>
          <path d="M18.5 18.5 27 27" stroke="#fff" stroke-width="4" stroke-linecap="round"/>
          <path d="M12 7.5v9M7.5 12h9" stroke="#fff" stroke-width="2.5"/>
        </svg>
      </div>
      <div class="card-caption"><h3>Sit Amet Consectetur</h3><p>Lorem Ipsum</p></div>
    </div>
    <div class="card" style="left:439px">
      <div class="card-photo" role="img" aria-label="Photo of a kitchen with red wood cabinetry and a hooded range" style="background:linear-gradient(170deg,#d9c7ad,#9b3a22 55%,#c8b08e)"></div>
      <div class="card-caption"><h3>Adipisicing Elit</h3><p>Lorem Ipsum</p></div>
    </div>
    <div class="card" style="left:618px">
      <div class="card-photo" role="img" aria-label="Photo of an open kitchen with brown cabinets, island and stainless appliances" style="background:linear-gradient(165deg,#c9c2b8,#7a5238 55%,#a3825e)"></div>
      <div class="card-caption"><h3>Labore Et Dolore</h3><p>Lorem Ipsum</p></div>
    </div>
  </section>

  <footer class="site-footer">
    <nav class="footer-nav">
      <a href="#" class="is-active">Home</a>
      <a href="#">Our Gallery</a>
      <a href="#">Our Services</a>
      <a href="#">Warranty</a>
      <a href="#">Contact Us</a>
    </nav>
    <div class="social" aria-label="Social links">
      <a class="social-link" href="#" aria-label="Social link 1"></a>
      <a class="social-link" href="#" aria-label="Social link 2"></a>
      <a class="social-link" href="#" aria-label="Social link 3"></a>
      <a class="social-link" href="#" aria-label="Social link 4"></a>
      <a class="social-link" href="#" aria-label="Social link 5"></a>
      <a class="social-link" href="#" aria-label="Social link 6"></a>
    </div>
    <p class="copyright">Copyrights © 2015. Brambleoak Custom Cabinets . All Rights Reserved</p>
  </footer>

</div>
</body>
</html>
```